Equipment Finance Specialist I work with companies who need the funds to buy their equipment

I would like a business card that stands out on the shelves. I want to be able to hand it to someone and say WOW. This card should have my logo.
You can put color into it I am very open on design and color

What my company does is we deal with dealerships that sell equipment such as Dump Trucks garbage trucks tractors trailers. Customers get referred to us and depending on their time in business we will ask for the following items

Companies that have been in business for more than two years we have a credit application program up to 250K . With this program we need the following items Credit application filled out(which is what I would like to be able for the customer to click on my website to get.) as well as three current month bank statements.

Deals over 250k we will need the following items

2 years business tax returns
2 years personal tax returns
Profit & Loss statement
Personal Financial Statement

what we do
100% FINANCING
SEASONAL PAYMENTS
LOAN BALLOON PAYMENTS
TRAC LEASING
LOW-INTEREST REFINANCING RATES
DEBT CONSOLIDATION

We specialize in creative financing solutions and offer a variety of reliable, flexible and expandable lending choices.

Target Market(s)

Trucking Companies

Industry/Entity Type

Trucking Company

Contact Information for Business Card

* $250,000 Application only Program
* Loans from $30,000 to 5,000,000
* Competitive Interest Rates

Font styles to use
Serif
Sans Serif

Colors

Designer to choose colors to be used in the design.

Requirements
Must have
• On the back of the card.
• * $250,000 Application only Program
• * Loans from $30,000 to 5,000,000
• My name, email, website. address
• * Competitive Interest Rates
• * 100% Financing
Nice to have
• I want my logo to pop on the card
• My logo is the great one I would like to use
Should not have
• I am up for your creativity as well

```html
<!DOCTYPE html>
<html lang="en">
<head>
<meta charset="utf-8">
<title>Apex Lending — Business Card</title>
<link rel="stylesheet" href="https://fonts.googleapis.com/css2?family=Work+Sans:wght@400;500&display=swap">
<style>
  :root {
    --backdrop: #262628;
    --card: #1b1b1d;
    --card-edge: #2a2a2d;
    --silver: #dcdcdc;
    --silver-soft: #bdbdbd;
    --divider: #8a8a8a;
  }
  * { margin: 0; padding: 0; box-sizing: border-box; }
  html, body {
    width: 1200px;
    height: 900px;
    overflow: hidden;
    background: var(--backdrop);
    font-family: "Work Sans", Arial, sans-serif;
    color: var(--silver);
  }
  .canvas {
    position: relative;
    width: 1200px;
    height: 900px;
  }
  .card {
    position: absolute;
    left: 250px;
    width: 700px;
    height: 400px;
    background: var(--card);
    border: 1px solid var(--card-edge);
  }
  .card--front { top: 30px; }
  .card--back { top: 470px; }

  .brand {
    display: flex;
    align-items: center;
    gap: 18px;
    white-space: nowrap;
  }
  .brand__dot {
    width: 64px;
    height: 64px;
    border-radius: 50%;
    border: 3px solid var(--silver);
    flex: none;
  }
  .brand__name {
    font-weight: 500;
    font-size: 44px;
    letter-spacing: 2px;
    line-height: 1;
    color: var(--silver);
    text-transform: uppercase;
  }

  .card--front .brand {
    position: absolute;
    left: 50%;
    top: 44%;
    transform: translate(-50%, -50%);
  }

  .offers {
    position: absolute;
    left: 0;
    right: 0;
    bottom: 48px;
    display: flex;
    justify-content: center;
    flex-wrap: wrap;
    gap: 8px 26px;
    list-style: none;
    padding: 0 40px;
  }
  .offers__item {
    font-size: 13px;
    letter-spacing: 1.5px;
    text-transform: uppercase;
    color: var(--silver-soft);
    white-space: nowrap;
  }
  .offers__item::before {
    content: "";
    display: inline-block;
    width: 5px;
    height: 5px;
    border-radius: 50%;
    background: var(--silver-soft);
    margin-right: 9px;
    vertical-align: middle;
  }

  .card--back .brand {
    position: absolute;
    left: 40px;
    top: 170px;
  }
  .card--back .brand__dot { width: 48px; height: 48px; }
  .card--back .brand__name { font-size: 28px; }

  .divider {
    position: absolute;
    left: 385px;
    top: 88px;
    width: 2px;
    height: 200px;
    background: var(--divider);
  }

  .contact {
    position: absolute;
    left: 420px;
    top: 90px;
  }
  .contact__name {
    font-size: 26px;
    font-weight: 400;
    letter-spacing: 2px;
    text-transform: uppercase;
  }
  .contact__role {
    font-size: 15px;
    color: var(--silver-soft);
    margin-top: 4px;
    letter-spacing: 1px;
  }
  .contact__address {
    font-size: 17px;
    line-height: 24px;
    letter-spacing: 1px;
    margin-top: 26px;
  }
  .contact__list {
    list-style: none;
    margin-top: 16px;
  }
  .contact__item {
    display: flex;
    align-items: center;
    gap: 12px;
    font-size: 17px;
    line-height: 26px;
    letter-spacing: 1px;
  }
  .contact__icon {
    width: 13px;
    height: 13px;
    flex: none;
  }
</style>
</head>
<body>
<main class="canvas">

  <section class="card card--front" aria-label="Card front">
    <div class="brand">
      <span class="brand__dot"></span>
      <span class="brand__name">Apex Lending</span>
    </div>
    <ul class="offers">
      <li class="offers__item">$250,000 Application Only Program</li>
      <li class="offers__item">Loans from $30,000 to 5,000,000</li>
      <li class="offers__item">Competitive Interest Rates</li>
      <li class="offers__item">100% Financing</li>
    </ul>
  </section>

  <section class="card card--back" aria-label="Card back">
    <div class="brand">
      <span class="brand__dot"></span>
      <span class="brand__name">Apex Lending</span>
    </div>

    <div class="divider"></div>

    <div class="contact">
      <h1 class="contact__name">Daniel Reyes</h1>
      <p class="contact__role">Director</p>
      <p class="contact__address">1820 Ridgeway Dr.<br>Frisco, TX 75033</p>
      <ul class="contact__list">
        <li class="contact__item">
          <svg class="contact__icon" viewBox="0 0 16 16" aria-hidden="true">
            <path d="M3 1.5l3 .5 1 3.5-2 1.2a9 9 0 0 0 4.3 4.3l1.2-2 3.5 1 .5 3-1.8 1.5C6.7 14 2 9.3 1.5 3.3z" fill="none" stroke="#dcdcdc" stroke-width="1.4" stroke-linejoin="round"/>
          </svg>
          1300 555 014
        </li>
        <li class="contact__item">
          <svg class="contact__icon" viewBox="0 0 16 16" aria-hidden="true">
            <rect x="1.5" y="3" width="13" height="10" fill="none" stroke="#dcdcdc" stroke-width="1.4"/>
            <path d="M1.5 3.5L8 9l6.5-5.5" fill="none" stroke="#dcdcdc" stroke-width="1.4"/>
          </svg>
          info@apexlending.com
        </li>
        <li class="contact__item">
          <svg class="contact__icon" viewBox="0 0 16 16" aria-hidden="true">
            <circle cx="8" cy="8" r="6.5" fill="none" stroke="#dcdcdc" stroke-width="1.3"/>
            <ellipse cx="8" cy="8" rx="2.8" ry="6.5" fill="none" stroke="#dcdcdc" stroke-width="1.1"/>
            <path d="M1.5 8h13" stroke="#dcdcdc" stroke-width="1.1"/>
          </svg>
          www.apexlending.com
        </li>
      </ul>
    </div>
  </section>

</main>
</body>
</html>
```